Create a new business card

I’m looking to update my business card to make it match the rest of my brand. I will include my current website as well as what my vehicle designs look like, etc..
What my business currently services
Weekly maintenance pool openings / closings
Equipment repair, including pumps, heaters, salt systems, filters, etc.
We install automatic covers and maintain them as well as provide preventative maintenance

I would like to include my name.
Dorian Pelkin.
My title
Owner
My email
Dorian@tidewellnx.com
4015827160
Www.tidewellnx.com

```html
<!DOCTYPE html>
<html lang="en">
<head>
<meta charset="utf-8">
<title>Tidewell Pool Care – Business Card</title>
<link href="https://fonts.googleapis.com/css2?family=Nunito:wght@400;600;700;800&display=swap" rel="stylesheet">
<style>
  :root {
    --page: #f1f1f1;
    --navy: #1e2c5c;
    --blue-deep: #2c5ea6;
    --blue-bright: #2bb8e8;
    --splash: #1f7fa8;
    --orange: #f5a21b;
    --orange-light: #fdc21a;
    --white: #ffffff;
  }
  * { box-sizing: border-box; margin: 0; padding: 0; }
  html, body {
    width: 1075px; height: 1200px; overflow: hidden;
    background: var(--page);
    font-family: "Nunito", sans-serif;
  }
  .canvas { position: relative; width: 1075px; height: 1200px; }
  .card {
    position: absolute; left: 205px; width: 664px; height: 396px;
    overflow: hidden; color: var(--white);
  }
  .card--front { top: 187px; }
  .card--back  { top: 637px; background: var(--navy); }
  .card__bg { position: absolute; inset: 0; width: 100%; height: 100%; }

  .holder { position: absolute; left: 36px; top: 34px; }
  .holder__name { font-size: 33px; font-weight: 600; line-height: 1.1; }
  .holder__title { font-size: 26px; font-weight: 400; line-height: 1.2; }

  .contact { position: absolute; left: 0; right: 0; top: 270px; text-align: center; padding-left: 80px; }
  .contact__phone { font-size: 35px; font-weight: 700; letter-spacing: 3px; line-height: 1.1; }
  .contact__line { font-size: 23px; font-weight: 600; line-height: 1.3; }

  .brand {
    position: absolute; display: flex; align-items: center; gap: 10px;
    font-size: 27px; font-weight: 800; line-height: 1.05; color: var(--white);
  }
  .brand__dot { width: 22px; height: 22px; border-radius: 50%; background: var(--orange); flex: none; }
  .card--front .brand { left: 390px; top: 108px; }
  .card--back .brand { left: 230px; top: 118px; }

  .tagline {
    position: absolute; left: 0; right: 0; top: 272px; text-align: center;
    font-size: 30px; font-weight: 800; line-height: 1.3; text-transform: uppercase;
  }
</style>
</head>
<body>
<main class="canvas">

  <section class="card card--front">
    <svg class="card__bg" viewBox="0 0 664 396" preserveAspectRatio="none">
      <defs>
        <linearGradient id="front-sky" x1="0" y1="1" x2="1" y2="0">
          <stop offset="0" stop-color="var(--blue-deep)"/>
          <stop offset="1" stop-color="var(--blue-bright)"/>
        </linearGradient>
        <linearGradient id="front-arc" x1="0" y1="0" x2="1" y2="0">
          <stop offset="0" stop-color="var(--orange)"/>
          <stop offset="1" stop-color="var(--orange-light)"/>
        </linearGradient>
      </defs>
      <rect width="664" height="396" fill="url(#front-sky)"/>
      <g role="img" aria-label="Water splash illustration">
        <ellipse cx="520" cy="230" rx="150" ry="125" fill="var(--splash)" opacity="0.45"/>
      </g>
      <path d="M0 306 Q334 100 664 330 L664 396 L0 396 Z" fill="url(#front-arc)"/>
      <path d="M0 312 Q334 173 664 334 L664 396 L0 396 Z" fill="var(--navy)"/>
    </svg>

    <div class="holder">
      <p class="holder__name">Dorian Pelkin</p>
      <p class="holder__title">Owner</p>
    </div>

    <div class="brand"><span class="brand__dot"></span><span>Tidewell<br>Pool Care</span></div>

    <div class="contact">
      <p class="contact__phone">4015827160</p>
      <p class="contact__line">Dorian@tidewellnx.com</p>
      <p class="contact__line">Www.tidewellnx.com</p>
    </div>
  </section>

  <section class="card card--back">
    <svg class="card__bg" viewBox="0 0 664 396" preserveAspectRatio="none">
      <g role="img" aria-label="Water splash illustration">
        <ellipse cx="332" cy="170" rx="210" ry="150" fill="var(--splash)" opacity="0.45"/>
      </g>
    </svg>

    <div class="brand"><span class="brand__dot"></span><span>Tidewell<br>Pool Care</span></div>

    <p class="tagline">Specializing in gunite pools<br>Weekly service</p>
  </section>

</main>
</body>
</html>
```